Communication and Marketing agency needs a new presentation card

We are a group of communication and marketing agencies specialized in companies that are in the logistics and industrial sector. The head agency is TELVANO Grupo and the group consists of 4 agencies: TELVANO Media, TELVANO Digital, TELVANO Research and DifundeEnPantalla. We hace 4 offices in Spain (Madrid, Barcelona, Valencia and Murcia). We are looking for a clean and attractive design that transmits our experience, brand presence in the market and knowledge to those who receive the card.It has to maintain the colors of the logo that is attached.
Target Market(s)
logistics and industrial sector
Marketing department
Contact Information for Business Card
Clean and attractive design

```html
<!DOCTYPE html>
<html lang="es">
<head>
<meta charset="UTF-8">
<title>TELVANO Grupo – Business Card</title>
<link rel="stylesheet" href="https://fonts.googleapis.com/css2?family=Tinos:wght@400;700&display=swap">
<style>
  :root {
    --stage: #2b2d30;
    --brand-red: #b81d22;
    --brand-red-light: #c42228;
    --card-grey: #56575a;
    --ink-white: #ffffff;
  }
  html, body {
    margin: 0;
    padding: 0;
    width: 1200px;
    height: 900px;
    overflow: hidden;
    background: var(--stage);
  }
  .canvas {
    position: relative;
    width: 1200px;
    height: 900px;
    font-family: "Tinos", "Times New Roman", serif;
  }
  .card {
    position: absolute;
    left: 320px;
    width: 560px;
    height: 320px;
    border-radius: 22px;
    overflow: hidden;
    box-shadow: 0 14px 30px rgba(0,0,0,0.45);
  }
  .card--front {
    top: 110px;
    background: linear-gradient(135deg, var(--brand-red) 0%, var(--brand-red-light) 100%);
    color: var(--ink-white);
  }
  .card--back {
    top: 470px;
    background: var(--card-grey);
  }

  /* contact block */
  .contact {
    position: absolute;
    left: 34px;
    top: 30px;
  }
  .contact__name {
    margin: 0;
    font-size: 22px;
    font-weight: 700;
    line-height: 1.1;
  }
  .contact__position {
    margin: 2px 0 14px;
    font-size: 14px;
  }
  .contact__list {
    list-style: none;
    margin: 0;
    padding: 0;
  }
  .contact__item {
    display: flex;
    align-items: center;
    gap: 9px;
    font-size: 13px;
    line-height: 21px;
  }
  .contact__icon {
    width: 14px;
    height: 14px;
    flex: none;
  }
  .contact__label {
    display: inline-block;
    width: 44px;
  }

  /* wordmarks */
  .wordmark {
    position: absolute;
    text-align: right;
    font-weight: 400;
    line-height: 1;
  }
  .wordmark__name {
    display: block;
    letter-spacing: 3px;
  }
  .wordmark__sub {
    display: block;
  }
  .card--front .wordmark {
    right: 48px;
    top: 120px;
    color: var(--ink-white);
  }
  .card--front .wordmark__name { font-size: 46px; }
  .card--front .wordmark__sub { font-size: 28px; margin-top: 2px; }

  .card--back .wordmark {
    left: 50%;
    top: 50%;
    transform: translate(-50%, -50%);
    color: var(--brand-red-light);
  }
  .card--back .wordmark__name { font-size: 48px; }
  .card--back .wordmark__sub { font-size: 28px; margin-top: 2px; }

  /* agency row */
  .agencies {
    position: absolute;
    left: 34px;
    right: 34px;
    bottom: 22px;
    display: flex;
    justify-content: flex-start;
    gap: 34px;
    color: var(--ink-white);
  }
  .agency {
    text-align: right;
    line-height: 1;
  }
  .agency__name {
    display: block;
    font-size: 12px;
    letter-spacing: 1px;
  }
  .agency__sub {
    display: block;
    font-size: 9px;
    margin-top: 1px;
  }
</style>
</head>
<body>
<main class="canvas">

  <section class="card card--front" aria-label="Business card front">
    <div class="contact">
      <h1 class="contact__name">Your Name</h1>
      <p class="contact__position">Position</p>
      <ul class="contact__list">
        <li class="contact__item">
          <svg class="contact__icon" viewBox="0 0 14 14" aria-hidden="true">
            <circle cx="7" cy="7" r="7" fill="#fff"/>
            <path d="M4.3 3.6l1.4-.3.8 1.9-.9.7a5 5 0 0 0 2.5 2.5l.7-.9 1.9.8-.3 1.4c-3.5.2-6.3-2.6-6.1-6.1z" fill="#b81d22"/>
          </svg>
          <span><span class="contact__label">Office</span>: +0.000.000.0000</span>
        </li>
        <li class="contact__item">
          <svg class="contact__icon" viewBox="0 0 14 14" aria-hidden="true">
            <circle cx="7" cy="7" r="7" fill="#fff"/>
            <rect x="5" y="3.2" width="4" height="7.6" rx="0.8" fill="#b81d22"/>
            <rect x="5.7" y="4" width="2.6" height="5" fill="#fff"/>
          </svg>
          <span><span class="contact__label">Cell</span>: +0.000.000.0000</span>
        </li>
        <li class="contact__item">
          <svg class="contact__icon" viewBox="0 0 14 14" aria-hidden="true">
            <circle cx="7" cy="7" r="7" fill="#fff"/>
            <rect x="3.5" y="4.5" width="7" height="5" fill="#b81d22"/>
            <path d="M3.8 4.8L7 7.4l3.2-2.6" stroke="#fff" stroke-width="0.8" fill="none"/>
          </svg>
          <span>info@telvanogrupo.com</span>
        </li>
        <li class="contact__item">
          <svg class="contact__icon" viewBox="0 0 14 14" aria-hidden="true">
            <circle cx="7" cy="7" r="7" fill="#fff"/>
            <circle cx="7" cy="7" r="3.6" fill="none" stroke="#b81d22" stroke-width="0.9"/>
            <ellipse cx="7" cy="7" rx="1.5" ry="3.6" fill="none" stroke="#b81d22" stroke-width="0.8"/>
            <path d="M3.4 7h7.2" stroke="#b81d22" stroke-width="0.8"/>
          </svg>
          <span>www.telvanogrupo.com</span>
        </li>
        <li class="contact__item">
          <svg class="contact__icon" viewBox="0 0 14 14" aria-hidden="true">
            <circle cx="7" cy="7" r="7" fill="#fff"/>
            <path d="M7 11.2S4.3 8 4.3 6.1a2.7 2.7 0 0 1 5.4 0C9.7 8 7 11.2 7 11.2z" fill="#b81d22"/>
            <circle cx="7" cy="6.1" r="1" fill="#fff"/>
          </svg>
          <span>Office Address</span>
        </li>
      </ul>
    </div>

    <div class="wordmark">
      <span class="wordmark__name">TELVANO</span>
      <span class="wordmark__sub">Grupo</span>
    </div>

    <div class="agencies">
      <div class="agency">
        <span class="agency__name">TELVANO</span>
        <span class="agency__sub">Research</span>
      </div>
      <div class="agency">
        <span class="agency__name">TELVANO</span>
        <span class="agency__sub">Digital</span>
      </div>
      <div class="agency">
        <span class="agency__name">TELVANO</span>
        <span class="agency__sub">Media</span>
      </div>
    </div>
  </section>

  <section class="card card--back" aria-label="Business card back">
    <div class="wordmark">
      <span class="wordmark__name">TELVANO</span>
      <span class="wordmark__sub">Grupo</span>
    </div>
  </section>

</main>
</body>
</html>
```